Printer Cartridges Supplier Namecard

Attached is my company logo and the design of my current namecard. I would like to have a more special look for it. Can have a little cuteness too rather than those normal standard feel. I'm a supplier mainly dealing with original and compatible printer toner cartridges, some other products like paper supplies as well.

Target Market(s)

Companies, businesses, corporates

Industry/Entity Type

It Company

Contact Information for Business Card

Logo, name, contact, address, supplies and maybe a slogan

Colors
85cae6
33a6d7
3176b5
0255a3
0792cd
85abd2

Requirements
Must have
• Logo, name, contact and address basic details.
• Must include some pictures, not just rearrange what I'm currently having.
Nice to have
• Be creative and bold, a diiferent traditional feel.

```html
<!DOCTYPE html>
<html lang="en">
<head>
<meta charset="utf-8">
<title>tonerbay.sg – Business Card</title>
<link href="https://fonts.googleapis.com/css2?family=Roboto:wght@300;400&display=swap" rel="stylesheet">
<style>
  :root{
    --bg:#1e1e1f;
    --paper:#ffffff;
    --sky:#5ab4e6;
    --azure:#33a6d7;
    --mid-blue:#2f78bb;
    --deep-blue:#0d55a3;
    --ink-grey:#555558;
    --title-grey:#444447;
  }
  *{margin:0;padding:0;box-sizing:border-box}
  html,body{width:1200px;height:897px;overflow:hidden;background:var(--bg)}
  body{position:relative;font-family:'Roboto',Arial,sans-serif}
  .card{position:absolute;left:304px;width:594px;height:338px;background:var(--paper);border-radius:22px;overflow:hidden}
  .card--front{top:92px}
  .card--back{top:470px}
  .card__waves{position:absolute;inset:0;width:594px;height:338px}
  .brand{position:absolute;display:flex;align-items:center;color:var(--ink-grey);font-weight:400}
  .brand__mark{background:var(--sky);flex:none}
  .brand__tagline{position:absolute;color:var(--ink-grey);font-weight:300;white-space:nowrap}

  .card--front .brand{left:20px;top:36px;gap:14px}
  .card--front .brand__mark{width:66px;height:66px}
  .card--front .brand__name{font-size:38px;line-height:1}
  .card--front .brand__tagline{left:100px;top:92px;font-size:8.5px}

  .person{position:absolute;right:31px;top:36px;text-align:right}
  .person__name{color:var(--azure);font-size:19px;font-weight:400;letter-spacing:.3px}
  .person__title{color:var(--title-grey);font-size:13.5px;font-weight:300;letter-spacing:.8px;margin-top:1px}
  .person__mobile{color:var(--azure);font-size:13px;font-weight:400;letter-spacing:.8px;margin-top:12px}

  .contact{position:absolute;right:31px;top:203px;list-style:none;text-align:right;color:#fff;font-size:13.5px;font-weight:300}
  .contact li{display:flex;justify-content:flex-end;align-items:center;gap:7px;height:17px}
  .contact svg{width:9px;height:9px}
  .address{position:absolute;right:31px;top:272px;text-align:right;color:#fff;font-size:13.5px;font-weight:300;line-height:19px}

  .card--back .brand{left:86px;top:111px;gap:22px}
  .card--back .brand__mark{width:100px;height:100px}
  .card--back .brand__name{font-size:62px;line-height:1}
  .card--back .brand__tagline{left:244px;top:200px;font-size:12.5px}

  .services{position:absolute;top:285px;list-style:none;color:#fff;font-size:14.5px;font-weight:300;line-height:20px}
  .services li{display:flex;align-items:center;gap:12px}
  .services li::before{content:"";width:9px;height:9px;border-radius:50%;background:var(--sky)}
  .services--left{left:21px}
  .services--right{right:24px;text-align:right}
  .services--right li{flex-direction:row-reverse}
</style>
</head>
<body>

<section class="card card--front" aria-label="Business card front">
  <svg class="card__waves" viewBox="0 0 743 423" preserveAspectRatio="none" aria-hidden="true">
    <path d="M0,287 C100,330 250,320 371,237 C260,305 110,335 0,310 Z" fill="var(--sky)"/>
    <path d="M0,325 C120,355 250,350 380,265 C500,175 600,110 743,195 L743,423 L0,423 Z" fill="var(--mid-blue)"/>
    <path d="M50,372 C250,380 420,280 520,220 C600,175 680,162 722,180" fill="none" stroke="#fff" stroke-width="6" stroke-linecap="round"/>
  </svg>

  <div class="brand">
    <span class="brand__mark"></span>
    <span class="brand__name">tonerbay.sg</span>
  </div>
  <p class="brand__tagline">Compatible printer ink and toner solutions</p>

  <div class="person">
    <p class="person__name">MIRA LENZ</p>
    <p class="person__title">Sales Executive</p>
    <p class="person__mobile">HP 9845 1730</p>
  </div>

  <ul class="contact">
    <li>611-480-3275
      <svg viewBox="0 0 10 10"><path d="M2,1 L4,1 L4.6,3 L3.4,3.8 Q4.4,5.8 6.2,6.6 L7,5.4 L9,6 L9,8 Q5,9 1.6,5 Q1,2.6 2,1 Z" fill="#fff"/></svg>
    </li>
    <li>mira@tonerbay.sg
      <svg viewBox="0 0 10 10"><rect x="1" y="2.2" width="8" height="5.6" fill="none" stroke="#fff" stroke-width="1.2"/><path d="M1,2.6 L5,5.4 L9,2.6" fill="none" stroke="#fff" stroke-width="1"/></svg>
    </li>
    <li>www.tonerbay.sg
      <svg viewBox="0 0 10 10"><circle cx="5" cy="5" r="4" fill="none" stroke="#fff" stroke-width="1"/><ellipse cx="5" cy="5" rx="1.8" ry="4" fill="none" stroke="#fff" stroke-width=".8"/><path d="M1,5 H9" stroke="#fff" stroke-width=".8"/></svg>
    </li>
  </ul>

  <p class="address">47A Harbourview Lane<br>05-112 Singapore 518720</p>
</section>

<section class="card card--back" aria-label="Business card back">
  <svg class="card__waves" viewBox="0 0 742 423" preserveAspectRatio="none" aria-hidden="true">
    <path d="M0,330 C220,352 520,345 742,285 L742,423 L0,423 Z" fill="var(--deep-blue)"/>
    <path d="M150,342 C400,350 600,322 742,280 L742,296 C600,334 400,354 150,342 Z" fill="var(--sky)"/>
  </svg>

  <div class="brand">
    <span class="brand__mark"></span>
    <span class="brand__name">tonerbay.sg</span>
  </div>
  <p class="brand__tagline">Compatible printer ink and toner solutions</p>

  <ul class="services services--left">
    <li>Printer Ink &amp; Toner Cartridges</li>
    <li>Original Printer Cartridges</li>
  </ul>
  <ul class="services services--right">
    <li>Paper Products</li>
    <li>Printer Maintainence &amp; Repair</li>
  </ul>
</section>

</body>
</html>
```